We have a company that provide sandblasted stone products. Example: numbers for houses. Also we sell cultured stone,brick natural stone to the contractor,homeowner. We need to get a business card that describe our product and service. In the original idea we had an old fashion chisel striking through the x in velquarin.

Reason: We realized that 2 days was not enough time for the competion to be open many of the designers may be to busy and require more time to compete.

Industry/Entity Type

It Company

Logo Text

Velquarin

```html
<!DOCTYPE html>
<html lang="en">
<head>
<meta charset="utf-8">
<title>Velquarin — Identity and Business Card</title>
<link rel="stylesheet" href="https://fonts.googleapis.com/css2?family=Bebas+Neue&family=Oswald:wght@500;600&family=Open+Sans:wght@400&display=swap">
<style>
  :root {
    --banner-stone: #f4e6cb;
    --banner-vein: #f9edd3;
    --card-stone: #eddcc3;
    --card-vein: #ddc3a0;
    --ink: #0d0b0a;
    --ink-soft: #231f20;
    --steel: #4b4744;
    --muted: #6b6460;
    --rule: #5a5a5a;
    --paper: #ffffff;
  }
  * { box-sizing: border-box; margin: 0; padding: 0; }
  html, body { width: 1200px; height: 1000px; overflow: hidden; background: var(--paper); }
  .canvas { position: relative; width: 1200px; height: 1000px; }

  .brand-banner {
    position: absolute; left: 0; top: 0; width: 1200px; height: 468px;
    background: radial-gradient(ellipse at 60% 40%, var(--banner-vein), var(--banner-stone) 70%);
    border-bottom: 2px solid var(--rule);
  }
  .brand-mark { position: absolute; border-radius: 50%; background: var(--ink-soft); }
  .brand-banner .brand-mark { left: 507px; top: 43px; width: 170px; height: 170px; }
  .wordmark {
    position: absolute; font-family: "Bebas Neue", sans-serif; font-weight: 400; color: var(--ink);
    white-space: nowrap; line-height: 1;
  }
  .brand-banner .wordmark {
    left: 240px; width: 700px; top: 219px; text-align: center;
    font-size: 122px; letter-spacing: 26px; padding-left: 26px;
  }
  .tagline {
    position: absolute; font-family: "Bebas Neue", sans-serif; font-weight: 400; color: var(--ink-soft);
    white-space: nowrap; line-height: 1;
  }
  .brand-banner .tagline { left: 240px; width: 700px; top: 355px; font-size: 28px; letter-spacing: 0.3px; text-align: center; }
  .tagline .sep { display: inline-block; margin: 0 6px; }

  .card {
    position: absolute; width: 525px; height: 299px; overflow: hidden;
    background: radial-gradient(ellipse at 55% 45%, var(--card-stone), #e8d3b4 80%);
  }
  .card-front { left: 15px; top: 483px; }
  .card-back { left: 548px; top: 641px; }
  .card .chevrons { position: absolute; left: 0; top: 0; }

  .holder-name {
    position: absolute; left: 125px; width: 200px; top: 30px; text-align: center;
    font-family: "Oswald", sans-serif; font-weight: 600; font-size: 29px; color: var(--ink-soft); line-height: 1;
  }
  .holder-role {
    position: absolute; left: 125px; width: 200px; top: 67px; text-align: center;
    font-family: "Oswald", sans-serif; font-weight: 500; font-size: 13px; color: var(--muted); line-height: 1;
  }
  .contact-list { list-style: none; }
  .contact-item { position: absolute; right: 0; height: 48px; display: flex; align-items: center; }
  .contact-text {
    font-family: "Open Sans", sans-serif; font-size: 11px; color: var(--ink-soft);
    margin-right: 11px; white-space: nowrap;
  }
  .contact-icon {
    width: 59px; height: 48px; background: var(--ink-soft); border-radius: 7px 0 0 7px;
    display: flex; align-items: center; justify-content: center;
  }
  .contact-icon svg { width: 30px; height: 30px; }

  .card-back .brand-mark { left: 317px; top: 43px; width: 82px; height: 82px; }
  .card-back .wordmark { left: 215px; top: 124px; font-size: 60px; letter-spacing: 8px; }
  .card-back .tagline { left: 215px; top: 189px; font-size: 13.5px; letter-spacing: 0.2px; }
  .card-back .tagline .sep { margin: 0 3px; }
</style>
</head>
<body>
<main class="canvas">

  <section class="brand-banner" role="img" aria-label="Cracked sandstone texture backdrop">
    <div class="brand-mark" aria-hidden="true"></div>
    <h1 class="wordmark">VELQUARIN</h1>
    <p class="tagline">Sandblasted Stone<span class="sep">✲</span>Cultured Stone<span class="sep">✲</span>Brick Natural Stone</p>
  </section>

  <article class="card card-front" aria-label="Business card front, cracked stone texture">
    <svg class="chevrons" width="525" height="299" viewBox="0 0 525 299" aria-hidden="true">
      <polyline points="0,20 115,150 0,280" fill="none" stroke="var(--steel)" stroke-width="24"/>
      <polyline points="38,-12 188,150 38,312" fill="none" stroke="var(--ink-soft)" stroke-width="30"/>
    </svg>
    <h2 class="holder-name">MAREK OLDEN</h2>
    <p class="holder-role">OWNER</p>
    <ul class="contact-list">
      <li class="contact-item" style="top:74px">
        <span class="contact-text">555.210.4817</span>
        <span class="contact-icon"><svg viewBox="0 0 24 24"><path fill="#fff" d="M6.6 10.8c1.4 2.8 3.8 5.1 6.6 6.6l2.2-2.2c.3-.3.7-.4 1-.2 1.1.4 2.3.6 3.6.6.6 0 1 .4 1 1V20c0 .6-.4 1-1 1C10.6 21 3 13.4 3 4c0-.6.4-1 1-1h3.5c.6 0 1 .4 1 1 0 1.3.2 2.5.6 3.6.1.3 0 .7-.2 1L6.6 10.8z" transform="rotate(90 12 12)"/></svg></span>
      </li>
      <li class="contact-item" style="top:126px">
        <span class="contact-text">marek@velquarin.com</span>
        <span class="contact-icon"><svg viewBox="0 0 24 24"><rect x="3" y="6" width="18" height="12" fill="#fff"/><polyline points="3,6 12,13 21,6" fill="none" stroke="var(--ink-soft)" stroke-width="1.4"/></svg></span>
      </li>
      <li class="contact-item" style="top:178px">
        <span class="contact-text">www.velquarin.com</span>
        <span class="contact-icon"><svg viewBox="0 0 24 24" fill="none" stroke="#fff" stroke-width="1.6"><circle cx="12" cy="12" r="9.5"/><ellipse cx="12" cy="12" rx="4.2" ry="9.5"/><line x1="12" y1="2.5" x2="12" y2="21.5"/><line x1="2.5" y1="12" x2="21.5" y2="12"/><line x1="4" y1="7.5" x2="20" y2="7.5"/><line x1="4" y1="16.5" x2="20" y2="16.5"/></svg></span>
      </li>
      <li class="contact-item" style="top:230px">
        <span class="contact-text">Here goes your address</span>
        <span class="contact-icon"><svg viewBox="0 0 24 24"><path fill="#fff" d="M12 3 2 12h3v9h5v-6h4v6h5v-9h3z"/></svg></span>
      </li>
    </ul>
  </article>

  <article class="card card-back" aria-label="Business card back, cracked stone texture">
    <svg class="chevrons" width="525" height="299" viewBox="0 0 525 299" aria-hidden="true">
      <polyline points="0,22 128,150 0,278" fill="none" stroke="var(--steel)" stroke-width="24"/>
      <polyline points="30,-12 183,150 30,312" fill="none" stroke="var(--ink-soft)" stroke-width="30"/>
    </svg>
    <div class="brand-mark" aria-hidden="true"></div>
    <h2 class="wordmark">VELQUARIN</h2>
    <p class="tagline">Sandblasted Stone<span class="sep">✲</span>Cultured Stone<span class="sep">✲</span>Brick Natural Stone</p>
  </article>

</main>
</body>
</html>
```